Moravel Aesthetic Doctor

I require an elegant, luxurious looking business card for my aesthetic business. I am a doctor and that will set me aside from competitors. I am planning to provide home and spa based treatments to clients with high expectations. I have attached my logo.

```html
<!DOCTYPE html>
<html lang="en">
<head>
<meta charset="utf-8">
<title>Moravel Aesthetic Doctor – Business Card</title>
<link rel="stylesheet" href="https://fonts.googleapis.com/css2?family=Cinzel:wght@400&family=Roboto:ital,wght@0,300;0,400;1,400&display=swap">
<style>
  :root {
    --backdrop: #3b3b3d;
    --card: #1f2022;
    --card-edge: #2a2b2e;
    --sky: #52b4ea;
    --silver: #c9d0d8;
    --white: #f4f6f8;
    --muted: #9aa0a6;
  }
  * { box-sizing: border-box; margin: 0; padding: 0; }
  html, body { width: 799px; height: 1200px; overflow: hidden; }
  body {
    background: var(--backdrop);
    font-family: "Roboto", Arial, sans-serif;
    position: relative;
  }
  .card {
    position: absolute;
    left: 80px;
    width: 640px;
    height: 366px;
    background: linear-gradient(160deg, var(--card-edge), var(--card) 60%);
    border-radius: 6px;
    overflow: hidden;
    box-shadow: 0 14px 30px rgba(0,0,0,.45);
  }
  .card--front { top: 110px; }
  .card--back { top: 700px; }

  /* front */
  .brand {
    position: absolute;
    left: 60px;
    top: 58px;
    display: flex;
    align-items: center;
    gap: 20px;
  }
  .brand__mark {
    width: 78px; height: 78px;
    border-radius: 50%;
    border: 3px solid var(--silver);
  }
  .brand__name {
    font-family: "Cinzel", Georgia, serif;
    font-weight: 400;
    color: var(--silver);
    line-height: 1.05;
  }
  .brand__name-main { display: block; font-size: 50px; letter-spacing: 2px; }
  .brand__name-sub { display: block; font-size: 20px; letter-spacing: 3px; }
  .services {
    position: absolute;
    left: 0; right: 0;
    top: 196px;
    text-align: center;
    color: var(--white);
    font-size: 17px;
    line-height: 1.4;
    font-weight: 400;
  }
  .services span.sep { margin: 0 8px; }
  .band {
    position: absolute;
    left: 0; right: 0;
    background: var(--sky);
    color: var(--white);
    display: flex;
    align-items: center;
  }
  .band--front {
    top: 278px;
    height: 42px;
    justify-content: center;
    font-size: 17px;
    letter-spacing: 1px;
  }

  /* back */
  .holder {
    position: absolute;
    left: 48px;
    top: 46px;
  }
  .holder__name {
    font-size: 26px;
    font-weight: 300;
    color: var(--silver);
  }
  .holder__post {
    font-size: 12px;
    font-style: italic;
    color: var(--sky);
    margin-top: 4px;
  }
  .holder__diploma {
    font-size: 15px;
    color: var(--sky);
    margin-top: 3px;
  }
  .contact {
    position: absolute;
    left: 48px;
    top: 196px;
    list-style: none;
    color: var(--silver);
    font-size: 15px;
    line-height: 1.55;
  }
  .contact li { display: flex; align-items: center; gap: 10px; }
  .contact svg { width: 13px; height: 13px; fill: var(--sky); }
  .social { gap: 8px !important; }
  .social__dot {
    width: 16px; height: 16px; border-radius: 50%;
    background: var(--sky); display: inline-block;
  }
  .band--back {
    left: 196px;
    top: 300px;
    height: 44px;
    border-radius: 22px 0 0 22px;
    justify-content: flex-end;
    padding-right: 60px;
    font-size: 17px;
  }
</style>
</head>
<body>

<section class="card card--front" aria-label="Card front">
  <div class="brand">
    <span class="brand__mark" aria-hidden="true"></span>
    <div class="brand__name">
      <span class="brand__name-main">MORAVEL</span>
      <span class="brand__name-sub">AESTHETIC DOCTOR</span>
    </div>
  </div>
  <p class="services">
    Dermal Injectables<span class="sep">|</span>Plasma Facials<span class="sep">|</span>Microneedling<br>
    Skin Boosters<span class="sep">|</span>Excessive Sweating
  </p>
  <div class="band band--front">HOME AND SPA BASED TREATMENTS</div>
</section>

<section class="card card--back" aria-label="Card back">
  <div class="holder">
    <p class="holder__name">Dr Elena Varga</p>
    <p class="holder__post">MRCPCH MD</p>
    <p class="holder__diploma">Australasian Diploma of Aesthetic Medicine</p>
  </div>
  <ul class="contact">
    <li><svg viewBox="0 0 24 24"><path d="M6.6 10.8a15 15 0 0 0 6.6 6.6l2.2-2.2a1 1 0 0 1 1-.25 11.4 11.4 0 0 0 3.6.57 1 1 0 0 1 1 1V20a1 1 0 0 1-1 1A17 17 0 0 1 3 4a1 1 0 0 1 1-1h3.5a1 1 0 0 1 1 1c0 1.25.2 2.45.57 3.57a1 1 0 0 1-.25 1z"/></svg>0800 555 014</li>
    <li><svg viewBox="0 0 24 24"><path d="M2 5h20v14H2z M3 6l9 7 9-7" /></svg>elena@moravel.co.nz</li>
    <li><svg viewBox="0 0 24 24"><path d="M12 2a10 10 0 1 0 0 20 10 10 0 0 0 0-20zm0 2c.9 1.2 1.6 2.6 2 4h-4c.4-1.4 1.1-2.8 2-4zM4.3 14a8 8 0 0 1 0-4h3.4a16 16 0 0 0 0 4zm5.7 0a14 14 0 0 1 0-4h4a14 14 0 0 1 0 4zm6.3 0a16 16 0 0 0 0-4h3.4a8 8 0 0 1 0 4z"/></svg>www.moravel.co.nz</li>
    <li class="social">Follow us on: <span class="social__dot"></span><span class="social__dot"></span></li>
  </ul>
  <div class="band band--back">Home &amp; Spa Based Treatments</div>
</section>

</body>
</html>
```